Kelvor Engineers: Why you should hire us keepsake

New design. Open to plastic cards. We are an engineering firm that designs cell phone towers and commercial buildings. Please check out our website www.kelvorstruct.com for more details. We want people to remember our card and for it to be useful if possible. We want the same look and feel on these cards to be translated to other marketing material we may need such as brochures.

Target Market(s)

Architects, Developers and Telecommunication Carriers

Industry/Entity Type

Engineering

Contact Information for Business Card

Card with our company colors, logo, and innovative design with elements related to our industry.

Font styles to use
Sans Serif

Colors
9bcb3c
abd036
0255a3

Requirements
Must have
• Sleek and hip design
Nice to have
• Bright lime green and navy coloring that pops with an innovative design.
Should not have
• A basic and boring design

```html
<!DOCTYPE html>
<html lang="en">
<head>
<meta charset="utf-8">
<title>Kelvor Engineers – Business Card</title>
<link href="https://fonts.googleapis.com/css2?family=Roboto:wght@400;500&family=Roboto+Condensed:wght@700&display=swap" rel="stylesheet">
<style>
  :root {
    --backdrop: #232323;
    --card-white: #f1f1f1;
    --lime: #00f000;
    --navy: #0b2d5e;
    --ink: #4a4a4a;
    --rule: #9a9a9a;
    --white: #ffffff;
  }
  * { margin: 0; padding: 0; box-sizing: border-box; }
  html, body { width: 1200px; height: 960px; overflow: hidden; }
  body {
    position: relative;
    background: var(--backdrop);
    font-family: "Roboto", Arial, sans-serif;
  }
  .card {
    position: absolute;
    width: 600px;
    height: 343px;
  }
  .card--front { left: 314px; top: 113px; background: var(--card-white); }
  .card--back  { left: 311px; top: 472px; background: var(--lime); }

  .wordmark {
    position: absolute;
    font-family: "Roboto Condensed", "Arial Narrow", sans-serif;
    font-weight: 700;
    text-transform: uppercase;
    white-space: nowrap;
    line-height: 1;
  }
  .card--front .wordmark {
    left: 36px; top: 56px;
    font-size: 42px;
    color: var(--lime);
  }
  .card--back .wordmark {
    left: 0; width: 100%; top: 140px;
    text-align: center;
    font-size: 52px;
    color: var(--navy);
  }

  .holder-name {
    position: absolute;
    right: 36px; top: 189px;
    font-family: "Roboto Condensed", "Arial Narrow", sans-serif;
    font-weight: 700;
    font-size: 21px;
    color: var(--lime);
    text-transform: uppercase;
    letter-spacing: 0.2px;
  }
  .name-tab {
    position: absolute;
    right: 0; top: 186px;
    width: 13px; height: 29px;
    background: var(--lime);
  }
  .name-rule {
    position: absolute;
    left: 36px; right: 36px; top: 222px;
    height: 1px;
    background: var(--rule);
  }

  .contact-list {
    position: absolute;
    left: 36px; top: 254px;
    list-style: none;
    font-size: 14.5px;
    color: var(--ink);
    line-height: 19px;
  }
  .contact-list li { display: flex; align-items: center; gap: 8px; }
  .contact-list svg { width: 13px; height: 13px; fill: var(--lime); flex: none; }

  .website {
    position: absolute;
    right: 37px; top: 291px;
    font-size: 14.5px;
    color: var(--ink);
    letter-spacing: 0.6px;
  }

  .tagline {
    position: absolute;
    left: 0; width: 100%; top: 266px;
    display: flex; justify-content: center; align-items: center; gap: 3px;
    font-weight: 500;
    font-size: 16.5px;
    color: var(--white);
    text-transform: uppercase;
  }
  .tagline::before, .tagline::after {
    content: ""; width: 30px; height: 1.5px; background: var(--white);
  }
  .offices {
    position: absolute;
    left: 0; width: 100%; top: 288px;
    text-align: center;
    font-size: 15px;
    color: var(--white);
    letter-spacing: 0.8px;
  }
</style>
</head>
<body>

  <section class="card card--front" aria-label="Business card front">
    <div class="wordmark">Kelvor Engineers</div>

    <div class="holder-name">Dana Whitfield Morrow</div>
    <div class="name-tab"></div>
    <div class="name-rule"></div>

    <ul class="contact-list">
      <li>
        <svg viewBox="0 0 24 24" aria-hidden="true"><path d="M6.6 10.8c1.4 2.8 3.8 5.1 6.6 6.6l2.2-2.2c.3-.3.7-.4 1-.2 1.1.4 2.3.6 3.6.6.6 0 1 .4 1 1V20c0 .6-.4 1-1 1C10.6 21 3 13.4 3 4c0-.6.4-1 1-1h3.5c.6 0 1 .4 1 1 0 1.3.2 2.5.6 3.6.1.3 0 .7-.2 1z"/></svg>
        404.555.0172
      </li>
      <li>
        <svg viewBox="0 0 24 24" aria-hidden="true"><path d="M7 1h10a2 2 0 0 1 2 2v18a2 2 0 0 1-2 2H7a2 2 0 0 1-2-2V3a2 2 0 0 1 2-2zm0 3v14h10V4z"/></svg>
        706.555.0148
      </li>
      <li>
        <svg viewBox="0 0 24 24" aria-hidden="true"><path d="M2 5h20v2l-10 6L2 7zm0 4.3l10 6 10-6V19H2z"/></svg>
        dmorrow@kelvorstruct.com
      </li>
    </ul>

    <div class="website">www.kelvorstruct.com</div>
  </section>

  <section class="card card--back" aria-label="Business card back">
    <div class="wordmark">Kelvor Engineers</div>
    <div class="tagline">Multi-Discipline Engineering</div>
    <div class="offices">Columbus | Nashville | Tulsa | Santa Fe</div>
  </section>

</body>
</html>
```